BrivoTerna. Lantern of the Steady Harvest. Business card

Professional business card for BrivoTerna (Lantern of the Steady Harvest)
My rationale: Strategy-> Execution-> Results-> Value that lead to the BrivoTerna name: We put the Lantern of the Steady Harvest.
We deliver value to our customers helping them at defining a good strategy (cyan arrow). 90% of well formulated strategies fail due to poor execution so we also consider strategical execution very important (green arrow). Due to the execution we obtain the results (blue arrow). Finally, the results provide feedback to redefine strategy, and the new strategy has to be executed and new results obtained providing new feedback and on and on. It's like a wheel that finally, must create corporate value: value for shareholders, staholders, employees, providers...-

Target Market(s)

CEOs and steering comitees , invewrnent funds

Industry/Entity Type

Business Consultant

Contact Information for Business Card

Teodoro Vinsquel
CEO & Founder
teodoro.vinsquel@brivoterna-example.com
Mobile: +34 655.803.912
www.brivoterna-example.com

Colors

Designer to choose colors to be used in the design.

Requirements
Nice to have
• Nice to hace the words: Strategy, execution, results
• Nice to vave the claim: Lantern of the Steady Harvest
• The three colors should be shown:
• cyan for STRATEGY
• green for EXECUTION
• blue for RESULTS
Should not have
• Complete black background

```html
<!DOCTYPE html>
<html lang="en">
<head>
<meta charset="utf-8">
<title>BrivoTerna – Business Card</title>
<link rel="stylesheet" href="https://fonts.googleapis.com/css2?family=Montserrat:wght@500;600;700;800&family=Open+Sans:wght@400&display=swap">
<style>
  :root {
    --backdrop: #d9d8d5;
    --paper: #ffffff;
    --royal: #22409c;
    --royal-deep: #14307f;
    --navy-tab: #0b3f7a;
    --lime: #9ccd3a;
    --cyan: #2bb4e8;
    --ink: #333a45;
  }
  * { margin: 0; padding: 0; box-sizing: border-box; }
  html, body {
    width: 1200px; height: 801px; overflow: hidden;
    background: var(--backdrop);
  }
  .stage {
    width: 1200px; height: 801px;
    display: flex; align-items: center; justify-content: center; gap: 40px;
  }
  .card {
    position: relative;
    width: 540px; height: 310px;
    overflow: hidden;
    box-shadow: 0 6px 18px rgba(0,0,0,0.18);
  }

  /* Front */
  .card--front { background: var(--paper); }
  .brand-front {
    position: absolute; top: 58px; right: 56px;
    font-family: "Montserrat", sans-serif; font-weight: 800;
    font-size: 40px; letter-spacing: -1px; color: var(--royal);
  }
  .holder { position: absolute; left: 44px; top: 128px; }
  .holder-name {
    font-family: "Montserrat", sans-serif; font-weight: 700;
    font-size: 21px; color: var(--royal);
  }
  .holder-role {
    font-family: "Montserrat", sans-serif; font-weight: 600;
    font-size: 15px; color: var(--lime); margin-top: 2px;
  }
  .contact-list {
    position: absolute; left: 44px; bottom: 42px; list-style: none;
    font-family: "Open Sans", sans-serif; font-size: 13.5px; color: var(--ink);
  }
  .contact-list li { display: flex; align-items: center; gap: 8px; line-height: 21px; }
  .contact-list svg { width: 13px; height: 13px; flex: none; }
  .edge-tab {
    position: absolute; left: -8px; top: 218px;
    width: 26px; height: 16px; border-radius: 6px; background: var(--navy-tab);
  }
  .edge-band { position: absolute; left: 0; right: 0; bottom: 0; height: 8px; display: flex; }
  .edge-band .seg-results { flex: 5; background: var(--royal); }
  .edge-band .seg-execution { flex: 3; background: var(--lime); }
  .edge-band .seg-strategy { flex: 3; background: var(--cyan); }

  /* Back */
  .card--back {
    background: linear-gradient(160deg, var(--royal) 0%, var(--royal) 55%, var(--royal-deep) 100%);
    display: flex; flex-direction: column; align-items: center; justify-content: center;
  }
  .brand-back {
    font-family: "Montserrat", sans-serif; font-weight: 800;
    font-size: 62px; letter-spacing: -2px; color: var(--paper);
  }
  .pillars {
    display: flex; gap: 16px; margin-top: 10px; list-style: none;
    font-family: "Montserrat", sans-serif; font-weight: 500;
    font-size: 17px; letter-spacing: 1px; color: var(--paper);
  }
  .pillars li { display: flex; align-items: center; gap: 7px; }
  .pillars li::before {
    content: ""; width: 8px; height: 8px; background: var(--lime);
  }
</style>
</head>
<body>
<main class="stage">
  <section class="card card--front" aria-label="Business card front">
    <div class="brand-front">BrivoTerna</div>
    <div class="holder">
      <p class="holder-name">Teodoro Vinsquel</p>
      <p class="holder-role">CEO &amp; Founder</p>
    </div>
    <ul class="contact-list">
      <li>
        <svg viewBox="0 0 14 14" aria-hidden="true"><rect x="3.5" y="1" width="7" height="12" rx="1.3" fill="none" stroke="#9ccd3a" stroke-width="1.4"/><circle cx="7" cy="10.8" r="0.8" fill="#9ccd3a"/></svg>
        +34 655.803.912
      </li>
      <li>
        <svg viewBox="0 0 14 14" aria-hidden="true"><rect x="1" y="3" width="12" height="8.5" fill="#9ccd3a"/><path d="M1 3 L7 8 L13 3 M1 11.5 L5.5 7 M13 11.5 L8.5 7" fill="none" stroke="#fff" stroke-width="1"/></svg>
        teodoro.vinsquel@brivoterna-example.com
      </li>
      <li>
        <svg viewBox="0 0 14 14" aria-hidden="true"><circle cx="7" cy="7" r="6" fill="#9ccd3a"/><path d="M1 7 H13 M7 1 C4 4 4 10 7 13 M7 1 C10 4 10 10 7 13" fill="none" stroke="#fff" stroke-width="0.9"/></svg>
        www.brivoterna-example.com
      </li>
    </ul>
    <span class="edge-tab"></span>
    <div class="edge-band">
      <span class="seg-results"></span><span class="seg-execution"></span><span class="seg-strategy"></span>
    </div>
  </section>

  <section class="card card--back" aria-label="Business card back">
    <div class="brand-back">BrivoTerna</div>
    <ul class="pillars">
      <li>Strategy</li>
      <li>Execution</li>
      <li>Results</li>
    </ul>
  </section>
</main>
</body>
</html>
```